Velmora Freightway Solutions Business cards

Would like a very unique design catchy but professional for business cards. Please use log provided.Marlon WellsCeo and Founder TransCon Logistix Solutions1-888-913-3225mwells@tlsolutionsus.comwww.tlsolutionsus.com

```html
<!DOCTYPE html>
<html lang="en">
<head>
<meta charset="utf-8">
<title>Velmora Freightway Solutions — Business Cards</title>
<link rel="stylesheet" href="https://fonts.googleapis.com/css2?family=Lato:wght@400;700;900&display=swap">
<style>
  :root {
    --stage: #1c1c1e;
    --card: #111113;
    --card-edge: #2a2a2d;
    --silver: #c9c9cc;
    --brand-blue: #1a7dc4;
    --brand-red: #e3262f;
    --ink: #e4e4e6;
    --rule: #4a4a4e;
  }
  * { margin: 0; padding: 0; box-sizing: border-box; }
  html, body {
    width: 1200px; height: 900px; overflow: hidden;
    background: var(--stage);
    font-family: "Lato", sans-serif;
  }
  .stage {
    position: relative; width: 1200px; height: 900px;
    display: flex; flex-direction: column; align-items: center; justify-content: center; gap: 44px;
  }
  .card {
    position: relative; width: 560px; height: 320px;
    background: var(--card);
    border: 1px solid var(--card-edge);
    border-radius: 26px;
  }
  /* Front */
  .card--front { display: flex; align-items: center; justify-content: center; }
  .front-name {
    font-weight: 900; font-size: 34px; letter-spacing: 1px;
    color: var(--silver); text-transform: uppercase; text-align: center; line-height: 1.15;
  }
  /* Back */
  .brand {
    position: absolute; top: 40px; right: 40px; text-align: right;
    font-weight: 900; font-size: 21px; letter-spacing: 1px;
    color: var(--brand-blue); text-transform: uppercase; line-height: 1.25;
  }
  .divider {
    position: absolute; left: 248px; right: 40px; top: 150px;
    height: 1px; background: var(--rule);
  }
  .website {
    position: absolute; right: 40px; top: 164px;
    font-size: 15px; font-weight: 700; color: var(--brand-blue);
  }
  .person { position: absolute; left: 40px; top: 132px; }
  .person-name {
    font-weight: 900; font-size: 22px; letter-spacing: 0.5px; text-transform: uppercase;
    color: var(--brand-blue);
  }
  .person-name .surname { color: var(--brand-red); }
  .person-title { font-size: 15px; color: var(--ink); margin-top: 2px; }
  .contacts { position: absolute; left: 40px; bottom: 38px; list-style: none; }
  .contacts li {
    display: flex; align-items: center; gap: 8px;
    font-size: 15px; color: var(--ink); line-height: 1.6;
  }
  .contacts svg { width: 14px; height: 14px; fill: var(--brand-blue); flex: none; }
</style>
</head>
<body>
<main class="stage">
  <section class="card card--front" aria-label="Card front">
    <p class="front-name">Velmora<br>Freightway</p>
  </section>

  <section class="card card--back" aria-label="Card back">
    <p class="brand">Velmora Freightway<br>Solutions</p>
    <div class="divider"></div>
    <p class="website">www.vfwayroutes.com</p>

    <div class="person">
      <p class="person-name">Dorian <span class="surname">Pike</span></p>
      <p class="person-title">CEO and Founder</p>
    </div>

    <ul class="contacts">
      <li>
        <svg viewBox="0 0 16 16" aria-hidden="true"><path d="M3.6 1.5l2.3 2.6-1.3 1.6c.9 2 2.5 3.6 4.6 4.6l1.6-1.3 2.6 2.3-1.3 2.2C7.5 13.2 2.8 8.5 1.4 3z"/></svg>
        1-888-470-6158
      </li>
      <li>
        <svg viewBox="0 0 16 16" aria-hidden="true"><path d="M1 3h14v10H1z M1.8 3.8L8 8.6l6.2-4.8" stroke="#111113" stroke-width="1.2"/></svg>
        dpike@vfwayroutes.com
      </li>
    </ul>
  </section>
</main>
</body>
</html>
```